BildeVOLD buisnesscard

Hey :) I need a modern buisnesscard for my company BildeVOLD
It most have:
Dagligleder og Fotograf: Henrik Audun Strandvik

Mob: +4791264085
Epost: post@bildevold.example
Adresse: Kvernbakken9, 6040 Langevåg

Facbook and instagram logo with text BildeVOLD

BildeVOLD logo

It Company

```html
<!DOCTYPE html>
<html lang="no">
<head>
<meta charset="utf-8">
<title>BildeVOLD – visittkort</title>
<link href="https://fonts.googleapis.com/css2?family=Noto+Sans:wght@400;700&display=swap" rel="stylesheet">
<style>
  :root {
    --stage: #e8e6e3;
    --card-dark: #262626;
    --frame-grey-light: #b4b5b5;
    --frame-grey-dark: #9a9b9b;
    --blade-light: #f4f4f4;
    --brand-blue: #3a8fc0;
    --brand-pink: #d5539a;
    --ink: #2a2a2a;
    --guide: #9c9c9c;
  }
  * { box-sizing: border-box; margin: 0; padding: 0; }
  html, body {
    width: 1200px; height: 1200px; overflow: hidden;
    background: var(--stage);
    font-family: "Noto Sans", Verdana, sans-serif;
  }
  .canvas { position: relative; width: 1200px; height: 1200px; }

  .card {
    position: absolute; left: 240px; width: 720px; height: 434px;
    overflow: hidden;
  }

  /* Front side */
  .card-front {
    top: 110px;
    background: linear-gradient(135deg, var(--frame-grey-light), var(--frame-grey-dark));
  }
  .viewfinder {
    position: absolute; left: 24px; top: 24px; width: 675px; height: 340px;
    background: var(--card-dark);
  }
  .corner { position: absolute; width: 40px; height: 40px; border-color: var(--guide); border-style: solid; border-width: 0; }
  .corner-tl { left: 14px; top: 15px; border-left-width: 1px; border-top-width: 1px; }
  .corner-tr { right: 14px; top: 15px; border-right-width: 1px; border-top-width: 1px; }
  .corner-bl { left: 14px; bottom: 18px; border-left-width: 1px; border-bottom-width: 1px; }
  .corner-br { right: 14px; bottom: 18px; border-right-width: 1px; border-bottom-width: 1px; }

  .holder-name {
    position: absolute; left: 0; right: 0; top: 142px; text-align: center;
    color: var(--brand-blue); font-size: 27px; letter-spacing: 0.3px;
  }
  .focus-dot {
    position: absolute; left: 50%; top: 190px; width: 16px; height: 16px;
    margin-left: -8px; border: 1px solid var(--guide); border-radius: 50%;
  }
  .focus-dot::after {
    content: ""; position: absolute; left: 3px; top: 3px; width: 8px; height: 8px;
    border: 1px solid var(--guide); border-radius: 50%;
  }
  .holder-role {
    position: absolute; left: 0; right: 0; top: 206px; text-align: center;
    color: var(--brand-pink); font-size: 17.5px;
  }
  .contact {
    position: absolute; left: 0; right: 0; top: 375px; text-align: center;
    color: var(--ink); font-size: 16.5px; line-height: 22px; letter-spacing: 0.2px;
  }

  /* Back side */
  .card-back { top: 626px; background: var(--blade-light); }
  .aperture { position: absolute; inset: 0; width: 720px; height: 434px; display: block; }
  .aperture .blade { fill: var(--card-dark); }

  .brand-name {
    position: absolute; left: 0; width: 722px; top: 205px; text-align: center;
    color: var(--brand-blue); font-size: 50px; font-weight: 700; letter-spacing: 0.5px;
  }
  .social {
    position: absolute; top: 391px; display: flex; align-items: center; gap: 11px;
    color: var(--brand-pink); font-size: 19px;
  }
  .social-facebook { left: 353px; }
  .social-instagram { left: 524px; }
  .social-dot {
    width: 32px; height: 32px; border: 2px solid var(--brand-pink); border-radius: 50%;
  }
</style>
</head>
<body>
<main class="canvas">

  <section class="card card-front" aria-label="Visittkort, forside">
    <div class="viewfinder">
      <span class="corner corner-tl"></span>
      <span class="corner corner-tr"></span>
      <span class="corner corner-bl"></span>
      <span class="corner corner-br"></span>
      <h1 class="holder-name">Henrik Audun Strandvik</h1>
      <span class="focus-dot"></span>
      <p class="holder-role">Dagligleder og Fotograf</p>
    </div>
    <p class="contact">
      M: 479 126 4085 | www.bildevold.example | post@bildevold.example<br>
      Kvernbakken9, 6040 Langevåg
    </p>
  </section>

  <section class="card card-back" aria-label="Visittkort, bakside">
    <svg class="aperture" viewBox="0 0 902 544" preserveAspectRatio="none" aria-hidden="true">
      <polygon class="blade" points="0,0 342,0 430,75 0,360"/>
      <polygon class="blade" points="402,0 707,0 645,195 478,78"/>
      <polygon class="blade" points="739,0 902,0 902,437 593,437"/>
      <polygon class="blade" points="342,465 902,465 902,544 365,544"/>
      <polygon class="blade" points="0,405 245,243 337,544 0,544"/>
    </svg>
    <p class="brand-name">BildeVOLD</p>
    <div class="social social-facebook"><span class="social-dot"></span><span>BildeVOLD</span></div>
    <div class="social social-instagram"><span class="social-dot"></span><span>BildeVOLD</span></div>
  </section>

</main>
</body>
</html>
```